Novexa company website, a website for employment for people with autism

The website will make a match between people and jobs, mainly in the graphical sector, but also other sectors.
The name of the company is novexa and automates jobs with people that are on the autism spectrum.
The whole matchmaking and feedback process and so doesn't have to be in this prototype, we just want the general information pages and to convey a great look and brand identity that we will keep in the other pages to be developed. The website must be made with Wordpress, since the backend will be developed in Wordpress too.
It is a social project that wants to create possibilites for people with ASS to work from home for an employer or to do a variety of tasks for different customers.
The people we hire are generally not on the regular job market or have difficulty finding a job and "selling themselves"

Target Market(s)

matchmaking between talent (with ASS) and employers / jobs

Number of Pages Required

5+ page

Font styles to use
Sans Serif

Colors
ec1f27
e34298
a64599
6b449b
0355a3
0792cd

Requirements
Must have
• A stunning landing pages
• Integrate our logo and must match with what will do. We want a clean, modern, minimalistic, sleek website that radiates creativity and good looks.
• We have one page describing what we can do for customers, one page for people with ASS that would like to be candidates (our approach, learning program, ...), two pages that are addressed to partners who want to cooperate: the one's that can assist with autism related assistance and the one's that can help with the job coaching.
Nice to have
• In our logo are many colors as we embrace diversity and want to show that. Out main branding colors are red (for action) and blue for stability and will all gradients that go with it. Mainly white or black (or anthracite) for other parts
Should not have
• We want a modern and minimalistic design, no fluffy designs with lots of ornaments.

```html
<!DOCTYPE html>
<html lang="en">
<head>
<meta charset="utf-8">
<title>Novexa – Work for people on the autism spectrum</title>
<link rel="stylesheet" href="https://fonts.googleapis.com/css2?family=Poppins:ital,wght@0,300;0,400;0,500;0,600;0,700;1,400&display=swap">
<style>
:root{
  --navy:#17388e;
  --pink:#d9287f;
  --magenta:#e34298;
  --purple:#6b449b;
  --blue:#0355a3;
  --sky:#0792cd;
  --ink:#1c1c1c;
  --text:#555;
  --dark:#1d1d1d;
  --white:#fff;
}
*{margin:0;padding:0;box-sizing:border-box}
html,body{width:1200px;height:3571px;overflow:hidden;background:var(--white)}
body{font-family:"Poppins",sans-serif;color:var(--ink);position:relative}
.abs{position:absolute}
a{color:inherit;text-decoration:none}

/* top bar */
.topbar{left:0;top:0;width:1200px;height:43px;background:var(--navy);color:var(--white);font-size:14px}
.topbar .contact{top:12px;display:flex;align-items:center;gap:10px}
.topbar svg{fill:var(--white)}
.social-top{right:124px;top:11px;display:flex;gap:10px}
.social-top span{width:21px;height:21px;border-radius:50%;background:var(--white);opacity:.85}
.search{left:866px;top:12px}

/* header */
.brand{left:112px;top:70px;display:flex;align-items:center;gap:12px}
.brand .mark{width:34px;height:34px;border-radius:50%;background:var(--magenta)}
.brand .name{font-size:30px;font-weight:600;letter-spacing:3px;color:var(--ink)}
.nav{top:77px;font-size:16px;font-weight:500}
.nav a{position:absolute;white-space:nowrap}

/* hero */
.hero-title{left:110px;top:262px;font-size:76px;font-weight:700;letter-spacing:2px;color:var(--purple)}
.hero-sub{left:112px;top:364px;width:420px;font-size:17px;line-height:28px;color:#222}
.btn{display:flex;align-items:center;justify-content:center;background:var(--pink);color:var(--white);font-weight:600;border-radius:30px}
.hero-btn{left:112px;top:457px;width:174px;height:57px;font-size:17px}
.scroll-down{left:112px;top:581px}
.hero-photos{left:528px;top:107px;width:672px;height:583px}
.deco{left:0;top:0}

/* about */
.about{left:0;top:762px;width:1200px;height:576px;background:linear-gradient(60deg,#d62a86 0%,#8a3a9b 45%,#2c3c9b 80%,#243a98 100%);color:var(--white);text-align:center}
.about .mark{left:577px;top:100px;width:46px;height:46px;border-radius:50%;background:rgba(255,255,255,.9)}
.about h2{position:absolute;left:0;width:1200px;top:150px;font-size:46px;font-weight:500}
.about p{position:absolute;left:180px;width:840px;font-size:17px;line-height:29px}
.about .btn{left:514px;top:424px;width:172px;height:57px;font-size:17px}

/* what we do */
.wwd-frame{left:95px;top:1469px;width:436px;height:371px;background:var(--pink)}
.wwd-photo{left:112px;top:1450px;width:436px;height:371px;background:linear-gradient(135deg,#b7583a 0%,#d7c1a8 45%,#3c6d83 100%)}
.wwd h2{position:absolute;left:586px;top:1440px;font-size:46px;font-weight:500}
.wwd p{position:absolute;left:586px;top:1515px;width:505px;font-size:16.5px;line-height:30.5px;color:var(--text)}
.wwd .btn{left:586px;top:1767px;width:174px;height:59px;font-size:17px}

/* testimonial */
.testi{left:0;top:1952px;width:1200px;height:508px;background:linear-gradient(180deg,#1d4f86 0%,#2c74b0 55%,#3b90c9 100%);color:var(--white);text-align:center}
.testi .quote{position:absolute;left:0;width:1200px;top:112px;font-size:15.5px;line-height:29px;font-style:italic}
.avatar{border-radius:50%;border:3px solid rgba(255,255,255,.8)}
.testi .line{left:386px;top:380px;width:428px;height:2px;background:rgba(255,255,255,.45)}
.testi .line i{position:absolute;left:176px;top:-1px;width:62px;height:4px;background:var(--white)}
.testi .who{position:absolute;left:0;width:1200px;top:398px;font-size:13px;font-weight:600;line-height:21px}

/* blog */
.card{top:2574px;width:314px}
.card .img{width:314px;height:202px;box-shadow:0 6px 16px rgba(0,0,0,.18)}
.card .date{position:absolute;left:19px;top:188px;width:138px;height:33px;background:var(--pink);color:var(--white);font-size:12px;display:flex;align-items:center;justify-content:center;gap:7px}
.card h3{margin-top:60px;font-size:18px;font-weight:500;color:#111}
.card .meta{margin-top:8px;display:flex;align-items:center;gap:8px;font-size:12px;font-weight:600;color:#333}
.card .meta svg{fill:var(--navy)}
.card p{margin-top:14px;font-size:14.5px;line-height:31px;color:var(--text)}
.card .more{display:block;margin-top:10px;font-size:13px;color:var(--pink);font-weight:500}

/* newsletter + footer */
.footer{left:0;top:3131px;width:1200px;height:440px;background:var(--dark);color:var(--white)}
.footer h2{position:absolute;left:140px;top:50px;font-size:40px;font-weight:600}
.footer .lead{position:absolute;left:140px;top:113px;width:520px;font-size:13.5px;line-height:29px;color:#ddd}
.email-input{left:710px;top:64px;width:350px;height:45px;background:var(--white);color:#777;font-size:14px;display:flex;align-items:center;justify-content:center}
.subscribe{left:710px;top:124px;width:350px;height:45px;background:var(--pink);font-size:15px;font-weight:600;display:flex;align-items:center;justify-content:center;letter-spacing:.5px}
.footer .rule{left:0;top:226px;width:1200px;height:1px;background:#444}
.footer .icons{left:142px;top:293px;display:flex;gap:17px}
.footer .icons span{width:40px;height:40px;border-radius:50%;border:1.5px solid #ddd;display:flex;align-items:center;justify-content:center}
.footer .links{left:140px;top:356px;font-size:13.5px;display:flex;gap:28px;color:#ddd}
.footer .mail{left:140px;top:404px;font-size:14px;text-decoration:underline}
.footer .copy{right:150px;top:404px;font-size:13px;color:#ddd}
</style>
</head>
<body>

<header>
  <div class="abs topbar">
    <div class="abs contact" style="left:112px">
      <svg width="13" height="13" viewBox="0 0 24 24"><path d="M6.6 10.8a15 15 0 0 0 6.6 6.6l2.2-2.2c.3-.3.7-.4 1-.2 1.1.4 2.3.6 3.6.6.6 0 1 .4 1 1V20c0 .6-.4 1-1 1A17 17 0 0 1 3 4c0-.6.4-1 1-1h3.5c.6 0 1 .4 1 1 0 1.3.2 2.5.6 3.6.1.3 0 .7-.2 1z"/></svg>
      <span>+49 5550 1200488</span>
    </div>
    <div class="abs contact" style="left:340px">
      <svg width="14" height="11" viewBox="0 0 24 18"><path d="M0 0h24v18H0zm2 2v1l10 7 10-7V2L12 9z"/></svg>
      <span>info@novexa.com</span>
    </div>
    <svg class="abs search" width="18" height="18" viewBox="0 0 24 24"><path d="M10 2a8 8 0 0 1 6.3 12.9l5.4 5.4-1.4 1.4-5.4-5.4A8 8 0 1 1 10 2zm0 2a6 6 0 1 0 0 12 6 6 0 0 0 0-12z"/></svg>
    <div class="abs social-top"><span></span><span></span><span></span><span></span><span></span></div>
  </div>

  <div class="abs brand"><span class="mark"></span><span class="name">NOVEXA</span></div>

  <nav class="abs nav" style="left:0;width:1200px">
    <a href="#" style="left:535px">Home</a>
    <a href="#" style="left:612px">About Us</a>
    <a href="#" style="left:712px">Services</a>
    <a href="#" style="left:808px">What We Do</a>
    <a href="#" style="left:936px">Blog</a>
    <a href="#" style="left:1001px">Contact Us</a>
  </nav>
</header>

<section class="hero">
  <svg class="abs deco" width="1200" height="700" fill="none" stroke-width="2.5">
    <circle cx="366" cy="98" r="12" stroke="#e34298"/>
    <path d="M0 180 L30 190 L0 205" stroke="#a64599"/>
    <path d="M236 234 L258 244 L238 254 Z" stroke="#e34298"/>
    <path d="M626 166 L648 164 L636 184 Z" stroke="#a64599"/>
    <circle cx="32" cy="346" r="14" stroke="#e34298"/>
    <circle cx="502" cy="412" r="8" stroke="#e34298"/>
    <circle cx="38" cy="455" r="6" stroke="#e34298"/>
    <path d="M392 464 L412 464 L402 478 Z" stroke="#e34298"/>
  </svg>
  <h1 class="abs hero-title">NOVEXA</h1>
  <p class="abs hero-sub">Novexa automates jobs with people that are on the autism spectrum</p>
  <a href="#" class="abs btn hero-btn">Contact Us</a>
  <svg class="abs scroll-down" width="42" height="42" viewBox="0 0 42 42" fill="none">
    <circle cx="21" cy="21" r="18" stroke="#6b449b" stroke-width="3"/>
    <path d="M13 18 L21 26 L29 18" stroke="#e34298" stroke-width="3"/>
  </svg>
  <svg class="abs hero-photos" viewBox="0 0 672 583" role="img" aria-label="Black and white photos of women working at a table, set in hexagon tiles">
    <defs>
      <linearGradient id="gray" x1="0" y1="0" x2="1" y2="1"><stop offset="0" stop-color="#e6e6e6"/><stop offset="1" stop-color="#8d8d8d"/></linearGradient>
    </defs>
    <g fill="url(#gray)" stroke="#fff" stroke-width="6">
      <polygon points="190,45 280,85 290,200 195,250 100,200 100,85"/>
      <polygon points="450,0 565,55 570,180 450,240 355,185 355,60"/>
      <polygon points="630,85 672,70 672,300 630,290 560,230 560,130"/>
      <polygon points="100,200 195,250 200,400 110,460 0,410 0,250"/>
      <polygon points="300,240 420,245 455,360 420,470 300,470 245,360"/>
      <polygon points="560,245 672,250 672,520 560,520 475,400 480,300"/>
    </g>
  </svg>
</section>

<section class="abs about">
  <span class="abs mark"></span>
  <h2>About Us</h2>
  <p style="top:225px">It is a social project that wants to create possibilites for people with ASS to work from home for an employer or to do a variety of tasks for different customers</p>
  <p style="top:298px">Lorem ipsum dolor sit amet, consectetur adipiscing elit, sed do eiusmod tempor incididunt ut labore et dolore magna aliqua. Ut enim ad minim veniam, quis nostrud exercitation ullamco laboris nisi</p>
  <a href="#" class="abs btn">Read More</a>
</section>

<section class="wwd">
  <div class="abs wwd-frame"></div>
  <div class="abs wwd-photo" role="img" aria-label="Photo of two young men smiling at a table with a map"></div>
  <h2>What We Do</h2>
  <p>Lorem ipsum dolor sit amet, consectetur adipiscing elit, sed do eiusmod tempor incididunt ut labore et dolore magna aliqua. Ut enim ad minim veniam, quis nostrud exercitation ullamco laboris nisi ut aliquip ex ea commodo consequat. Duis aute irure dolor in reprehenderit in voluptate velit esse cillum dolore eu fugiat nulla pariatur. Excepteur sint occaecat cupidatat non proident, sunt in culpa qui officia deserunt mollit anim id est laborum</p>
  <a href="#" class="abs btn">Read More</a>
</section>

<section class="abs testi" role="group" aria-label="Testimonials">
  <svg class="abs" style="left:582px;top:113px" width="38" height="26" viewBox="0 0 38 26" fill="#fff">
    <path d="M9 0a9 9 0 0 1 9 9c0 8-6 15-13 17l-1-3c4-2 6-5 6-7A9 9 0 0 1 9 0zm20 0a9 9 0 0 1 9 9c0 8-6 15-13 17l-1-3c4-2 6-5 6-7a9 9 0 0 1-1-16z"/>
  </svg>
  <p class="quote" style="top:176px">"Lorem ipsum dolor sit amet, consectetur adipiscing elit, sed do eiusmod tempor incididunt ut labore et dolore<br>magna aliqua. Ut enim ad minim veniam, quis nostrud exercitation ullamco laboris nisi ut aliquip ex ea"</p>
  <svg class="abs" style="left:408px;top:300px" width="14" height="20" fill="none" stroke="#fff" stroke-width="2.5"><path d="M11 2 L3 10 L11 18"/></svg>
  <svg class="abs" style="left:767px;top:300px" width="14" height="20" fill="none" stroke="#fff" stroke-width="2.5"><path d="M3 2 L11 10 L3 18"/></svg>
  <div class="abs avatar" role="img" aria-label="Portrait photo of a client" style="left:458px;top:279px;width:62px;height:62px;background:linear-gradient(#c9c1b4,#7d756b)"></div>
  <div class="abs avatar" role="img" aria-label="Portrait photo of Mara L" style="left:553px;top:268px;width:84px;height:84px;background:linear-gradient(#e7cfa9,#a6805a)"></div>
  <div class="abs avatar" role="img" aria-label="Portrait photo of a client" style="left:666px;top:279px;width:62px;height:62px;background:linear-gradient(#d7d2cc,#8a837c)"></div>
  <div class="abs line"><i></i></div>
  <p class="who">MARA L<br>HALIFAX,NS</p>
</section>

<section class="blog">
  <article class="abs card" style="left:112px">
    <div class="img" role="img" aria-label="Photo of hands joining puzzle pieces" style="background:linear-gradient(135deg,#f2d6b0,#c9925f 60%,#7a92a8)"></div>
    <span class="date"><svg width="12" height="12" viewBox="0 0 12 12" fill="#fff"><path d="M1 2h10v9H1zM2 5v5h8V5zM3 0h1v3H3zm5 0h1v3H8z"/></svg>JULY,9 2018</span>
    <h3>SED UT PERSPICIATIS UNDE</h3>
    <div class="meta"><svg width="11" height="12" viewBox="0 0 11 12"><circle cx="5.5" cy="3" r="3"/><path d="M0 12a5.5 5.5 0 0 1 11 0z"/></svg>KATEOREEN<svg style="margin-left:16px" width="12" height="11" viewBox="0 0 12 11"><path d="M6 0c3.3 0 6 2 6 4.5S9.3 9 6 9L2 11l1-3C1 7 0 6 0 4.5 0 2 2.7 0 6 0z"/></svg>45</div>
    <p>Duis aute irure dolor in reprehenderit intate velit esse cillum dolore eu fugiat nullatur. Excepteur sint occaecat cupidatat...</p>
    <a href="#" class="more">Read More ›</a>
  </article>
  <article class="abs card" style="left:443px">
    <div class="img" role="img" aria-label="Photo of a man in a red checked shirt in a garden" style="background:linear-gradient(160deg,#3f5a34,#6f7d4a 45%,#8e2a2a 75%,#3b3b3b)"></div>
    <span class="date"><svg width="12" height="12" viewBox="0 0 12 12" fill="#fff"><path d="M1 2h10v9H1zM2 5v5h8V5zM3 0h1v3H3zm5 0h1v3H8z"/></svg>JULY,9 2018</span>
    <h3>SED UT PERSPICIATIS UNDE</h3>
    <div class="meta"><svg width="11" height="12" viewBox="0 0 11 12"><circle cx="5.5" cy="3" r="3"/><path d="M0 12a5.5 5.5 0 0 1 11 0z"/></svg>KATEOREEN<svg style="margin-left:16px" width="12" height="11" viewBox="0 0 12 11"><path d="M6 0c3.3 0 6 2 6 4.5S9.3 9 6 9L2 11l1-3C1 7 0 6 0 4.5 0 2 2.7 0 6 0z"/></svg>45</div>
    <p>Duis aute irure dolor in reprehenderit intate velit esse cillum dolore eu fugiat nullatur. Excepteur sint occaecat cupidatat...</p>
    <a href="#" class="more">Read More ›</a>
  </article>
  <article class="abs card" style="left:774px">
    <div class="img" role="img" aria-label="Photo of wooden game pieces in a wooden frame" style="background:linear-gradient(135deg,#d8d2c8,#a37652 55%,#6e4b33)"></div>
    <span class="date"><svg width="12" height="12" viewBox="0 0 12 12" fill="#fff"><path d="M1 2h10v9H1zM2 5v5h8V5zM3 0h1v3H3zm5 0h1v3H8z"/></svg>JULY,9 2018</span>
    <h3>SED UT PERSPICIATIS UNDE</h3>
    <div class="meta"><svg width="11" height="12" viewBox="0 0 11 12"><circle cx="5.5" cy="3" r="3"/><path d="M0 12a5.5 5.5 0 0 1 11 0z"/></svg>KATEOREEN<svg style="margin-left:16px" width="12" height="11" viewBox="0 0 12 11"><path d="M6 0c3.3 0 6 2 6 4.5S9.3 9 6 9L2 11l1-3C1 7 0 6 0 4.5 0 2 2.7 0 6 0z"/></svg>45</div>
    <p>Duis aute irure dolor in reprehenderit intate velit esse cillum dolore eu fugiat nullatur. Excepteur sint occaecat cupidatat...</p>
    <a href="#" class="more">Read More ›</a>
  </article>
</section>

<footer class="abs footer">
  <h2>Get more Information</h2>
  <p class="lead">Sed ut perspiciatis unde omnis iste natus error sit voluptatem accusantium doloremque laudantium, totam rem aperiam</p>
  <div class="abs email-input">Enter Your Email</div>
  <div class="abs subscribe">SUBSCRIBE NOW</div>
  <div class="abs rule"></div>
  <div class="abs icons">
    <span></span>
    <span><svg width="16" height="12" viewBox="0 0 24 18" fill="#fff"><path d="M0 0h24v18H0zm2 2v1l10 7 10-7V2L12 9z"/></svg></span>
    <span></span>
    <span></span>
    <span></span>
  </div>
  <nav class="abs links"><a href="#">Home</a><a href="#">About Us</a><a href="#">Services</a><a href="#">What We Do</a><a href="#">Blog</a><a href="#">Contact Us</a></nav>
  <a href="#" class="abs mail">info@novexa.com</a>
  <p class="abs copy">Copyright the Company Name 2019 | All Rights Reserved</p>
</footer>

</body>
</html>
```